Halvik - consultancy website

I need a new design for my webpage/presence [to be functioning with Wordpress - I have a programmer to set it up but not the design idea].
My company is Halvik - a consultancy firm focused on growth management for Swedish SME's primarily;. We call it Leadership toolkit for firms on the rise, kind of a doctor helping small become big. Contentwise, its a simple frontpage + 3-4 subpages with content re company/myself/focus etc. The new site should communicate a fresh, trustworthy take yet simple and functional on all devices [i.e. think UI compatible for mobile/tablet]. Current building parts/form elements are
a) existing logo and text elements
b) existing pictures
c) the yellowish color
colours and new ideas on pictures/positioning are welcome. I prefer a 'full width page' solution with centralised text elements but that's all up to you to suggest. Current site is a quickfix made by myself - now I'm moving it to a new platform so want to take the opportunity to make it
Nothing superspecial as it is a 2-man show; on the other hand I still want to have a modern & fresh reflection of my brand in digital environments. Help me out!
www.halvik-demo.se
Best
Lina Bergqvist

```html
<!DOCTYPE html>
<html lang="en">
<head>
<meta charset="utf-8">
<title>Halvik – What We Do</title>
<link rel="stylesheet" href="https://fonts.googleapis.com/css2?family=Lora:wght@400;700&family=Open+Sans:ital,wght@0,400;0,600;0,700;1,400&display=swap">
<style>
:root{
  --orange:#ee8428;
  --orange-line:#d97420;
  --ink:#333;
  --muted:#777;
  --footer:#3b3b3b;
  --footer-deep:#333;
  --footer-text:#e6e6e6;
  --white:#fff;
}
*{margin:0;padding:0;box-sizing:border-box}
html,body{width:701px;height:1200px;overflow:hidden;background:var(--white)}
body{position:relative;font-family:'Open Sans',sans-serif;color:var(--ink)}
.abs{position:absolute}
.brand{left:55px;top:16px;font-family:'Lora',serif;font-size:27px;color:#222;line-height:1}
.tagline{left:58px;top:44px;font-family:'Lora',serif;font-size:9.5px;color:#222}
.search{left:475px;top:27px;width:168px;height:23px;border:1px solid #ccc;border-radius:2px;font-size:8px;color:#999;padding:6px 10px}
.search svg{position:absolute;right:9px;top:6px}
.nav{left:0;top:73px;width:701px;height:31px;background:var(--orange)}
.nav ul{list-style:none;display:flex;margin-left:58px;width:587px;height:100%;border-left:1px solid var(--orange-line)}
.nav li{flex:1;text-align:center;font-family:'Lora',serif;font-size:8.5px;color:var(--white);line-height:31px;border-right:1px solid var(--orange-line)}
.hero{left:0;top:104px;width:701px;height:242px;background:linear-gradient(180deg,#8a9aa8 0%,#6f7d88 55%,#4f6672 78%,#5f8a96 100%)}
.hero-title{left:0;top:104px;width:701px;height:242px;display:flex;align-items:center;justify-content:center;font-family:'Lora',serif;font-weight:700;font-size:31px;color:var(--white);text-shadow:0 1px 3px rgba(0,0,0,.35)}
.section-title{left:0;top:365px;width:701px;text-align:center;font-family:'Lora',serif;font-size:14.5px;font-weight:700;color:#333}
.intro{left:120px;top:392px;width:461px;text-align:center;font-size:7.2px;line-height:13.6px;color:#555}
.card{width:179px}
.card .photo{width:179px;height:116px;border:1px solid #ddd;border-radius:2px}
.card h3{font-family:'Lora',serif;font-size:8.6px;font-weight:700;color:#333;margin-top:11px}
.card p{font-size:7px;line-height:13.6px;color:#666;margin-top:6px}
.card .more{display:block;font-size:7.2px;font-weight:700;color:var(--orange);margin-top:8px}
.testimonials{left:0;top:899px;width:701px;height:134px;background:var(--orange);color:var(--white);text-align:center}
.testimonials h2{font-family:'Lora',serif;font-size:14.5px;font-weight:700;margin-top:17px}
.testimonials blockquote{width:470px;margin:10px auto 0;font-style:italic;font-size:6.8px;line-height:15px}
.testimonials .who{font-size:9px;margin-top:7px}
.testimonials .role{font-style:italic;font-size:7px;margin-top:6px}
.footer{left:0;top:1033px;width:701px;height:132px;background:var(--footer);color:var(--footer-text)}
.footer h4{position:absolute;top:19px;font-family:'Lora',serif;font-size:8.6px;font-weight:700;color:var(--white)}
.footer p{position:absolute;font-size:7px;line-height:12.8px}
.divider{position:absolute;top:14px;width:1px;height:110px;background:#474747}
.email{position:absolute;left:237px;top:70px;width:200px;height:19px;background:#555;font-size:7px;color:#aaa;padding:5px 7px}
.subscribe{position:absolute;left:237px;top:97px;width:57px;height:19px;background:var(--orange);color:var(--white);font-size:7px;font-weight:700;text-align:center;line-height:19px;border-radius:2px}
.bottom{left:0;top:1165px;width:701px;height:35px;background:var(--footer-deep);border-top:1px solid #4a4a4a;color:var(--white)}
.bottom .copy{position:absolute;left:57px;top:12px;font-size:7px}
.social{position:absolute;top:10px;display:flex;gap:9px;left:541px}
.social span{width:13px;height:13px;background:#eee;border-radius:2px}
</style>
</head>
<body>
<header>
  <div class="abs brand">Halvik.</div>
  <div class="abs tagline">Leadership toolkit for firms on the rise</div>
  <div class="abs search">Search...
    <svg width="10" height="10" viewBox="0 0 10 10"><circle cx="4" cy="4" r="3" fill="none" stroke="#888" stroke-width="1.3"/><line x1="6.3" y1="6.3" x2="9" y2="9" stroke="#888" stroke-width="1.4"/></svg>
  </div>
</header>
<nav class="abs nav"><ul><li>Home</li><li>About us</li><li>What we Do</li><li>Who We Are</li><li>Why Halvik</li><li>Contact us</li></ul></nav>

<div class="abs hero" role="img" aria-label="Photo of a city skyline with high-rise towers across a harbour"></div>
<div class="abs hero-title">What We Do</div>
<svg class="abs" style="left:20px;top:215px" width="14" height="20" viewBox="0 0 14 20"><polyline points="11,2 3,10 11,18" fill="none" stroke="#fff" stroke-width="2.5"/></svg>
<svg class="abs" style="left:668px;top:215px" width="14" height="20" viewBox="0 0 14 20"><polyline points="3,2 11,10 3,18" fill="none" stroke="#fff" stroke-width="2.5"/></svg>

<h1 class="abs section-title">What We Do</h1>
<p class="abs intro">Consultancy services aiming to help high-performing organizations adapt to change and evolving economic conditions. Halvik delivers structure, means and orchestration to help growing companies develop healthy – where in-house competencies or bandwidth is simply not enough to implement a qualitative approach and lead on through.</p>

<article class="abs card" style="left:57px;top:456px">
  <div class="photo" role="img" aria-label="Photo of a girl looking up at growth marks on a white wall" style="background:linear-gradient(135deg,#f4f4f4,#e6e2de)"></div>
  <h3>Growth Management</h3>
  <p>Halvik delivers structure, means and orchestration to help growing companies develop healthy – where in-house competencies or bandwidth .</p>
  <span class="more">READ MORE &gt;&gt;</span>
</article>
<article class="abs card" style="left:262px;top:456px">
  <div class="photo" role="img" aria-label="Photo of a business meeting around a conference table with a presentation screen" style="background:linear-gradient(135deg,#c9ccd0,#5a5f66)"></div>
  <h3>Corporate communications</h3>
  <p>Halvik delivers structure, means and orchestration to help growing companies develop healthy – where in-house competencies or bandwidth .</p>
  <span class="more">READ MORE &gt;&gt;</span>
</article>
<article class="abs card" style="left:464px;top:456px">
  <div class="photo" role="img" aria-label="Illustration of business people assembling large gears on a meadow" style="background:linear-gradient(180deg,#b8b4a6,#8f8e7a 65%,#7a8a55)"></div>
  <h3>Organizational development</h3>
  <p>Halvik delivers structure, means and orchestration to help growing companies develop healthy – where in-house competencies or bandwidth .</p>
  <span class="more">READ MORE &gt;&gt;</span>
</article>
<article class="abs card" style="left:57px;top:676px">
  <div class="photo" role="img" aria-label="Photo of a hand holding a kite string against a cloudy sky" style="background:linear-gradient(160deg,#9ec4cc,#dfe9ea)"></div>
  <h3>Gap analysis &amp; field research papers</h3>
  <p>Halvik delivers structure, means and orchestration to help growing companies develop healthy – where in-house competencies or bandwidth .</p>
  <span class="more">READ MORE &gt;&gt;</span>
</article>
<article class="abs card" style="left:262px;top:676px">
  <div class="photo" role="img" aria-label="Photo of a team working together over documents at a desk" style="background:linear-gradient(135deg,#8a7460,#c9b39a)"></div>
  <h3>Project management</h3>
  <p>Halvik delivers structure, means and orchestration to help growing companies develop healthy – where in-house competencies or bandwidth .</p>
  <span class="more">READ MORE &gt;&gt;</span>
</article>
<article class="abs card" style="left:464px;top:676px">
  <div class="photo" role="img" aria-label="Photo of two hands passing a puzzle piece" style="background:linear-gradient(135deg,#7e8aa6,#d8c8c4)"></div>
  <h3>Conceptualizing</h3>
  <p>Halvik delivers structure, means and orchestration to help growing companies develop healthy – where in-house competencies or bandwidth .</p>
  <span class="more">READ MORE &gt;&gt;</span>
</article>

<section class="abs testimonials">
  <h2>Testimonials</h2>
  <blockquote>“ Important deliverables under Lina's responsibility has involved not only the creation of many successful creative product strategies, but also constructing efficient process flows and forming organizational structures to meet with market developments. ”</blockquote>
  <div class="who">- Mats Ekholm</div>
  <div class="role">( Former CEO of Nordvik Group )</div>
  <svg class="abs" style="left:52px;top:62px" width="10" height="14" viewBox="0 0 10 14"><polyline points="8,2 3,7 8,12" fill="none" stroke="#fff" stroke-width="2"/></svg>
  <svg class="abs" style="left:638px;top:62px" width="10" height="14" viewBox="0 0 10 14"><polyline points="2,2 7,7 2,12" fill="none" stroke="#fff" stroke-width="2"/></svg>
</section>

<footer class="abs footer">
  <h4 style="left:57px">About us</h4>
  <p style="left:57px;top:44px;width:140px">The Halvik properties are described as remarkably robust, delivering seamless entanglement across any partition and acting as a sophisticated enabler when applied into operations.</p>
  <div class="divider" style="left:211px"></div>
  <h4 style="left:237px">Newsletter Subscription</h4>
  <p style="left:237px;top:43px;width:180px;line-height:11px">Register Your Email Address To get Information About us</p>
  <div class="email">Email Address</div>
  <div class="subscribe">SUBSCRIBE</div>
  <div class="divider" style="left:466px"></div>
  <h4 style="left:492px">Contact Us</h4>
  <svg class="abs" style="left:491px;top:44px" width="8" height="11" viewBox="0 0 8 11"><path d="M4 0a4 4 0 0 1 4 4c0 3-4 7-4 7S0 7 0 4a4 4 0 0 1 4-4z" fill="#eee"/><circle cx="4" cy="4" r="1.5" fill="#3b3b3b"/></svg>
  <p style="left:511px;top:44px;width:135px;line-height:11.5px">classical Latin literature 45 BC, making it over 2000 Fjällby</p>
  <svg class="abs" style="left:491px;top:78px" width="9" height="9" viewBox="0 0 9 9"><path d="M1 0h2l1 2-1.2 1.2a6 6 0 0 0 3 3L7 5l2 1v2a1 1 0 0 1-1 1A8 8 0 0 1 0 1a1 1 0 0 1 1-1z" fill="#eee"/></svg>
  <p style="left:513px;top:76px">+46 [0] 700 00 12 34</p>
  <svg class="abs" style="left:490px;top:102px" width="11" height="8" viewBox="0 0 11 8"><rect width="11" height="8" rx="1" fill="#eee"/><polyline points="0.5,0.5 5.5,4.5 10.5,0.5" fill="none" stroke="#3b3b3b" stroke-width="1"/></svg>
  <p style="left:515px;top:100px;text-decoration:underline">info@halvik-demo.se</p>
</footer>
<div class="abs bottom">
  <div class="copy">Copyrights © Halvik 2015 . All rights Reserved.</div>
  <div class="social"><span></span><span></span><span></span><span></span><span></span></div>
</div>
</body>
</html>
```